Manuka Honey company needs a Upmarket, Luxury Website!

New Zealand, Taranaki based Manuka Honey company Rimu Vale Honey is looking for a new website, we are looking for an upmarket, luxury, serious website design. We export the highest quality quality Manuka Honey, straight from the Taranaki region.

Main export markets are Asia & Europe, also New Zealand & Australia.

Looking to have a beautiful, upmarket, serious, luxurious & graphical experience with mobile optimization in mind. Like the use of product staging/mockups

You can use copy from other websites to build the site and we will change the copy after the design is finished.

***Please include 'Honey Product' mockups in website.

*Will add illustrator files in coming days***

Feel free to make website functional in Shopify, Wordpress or WIX

Target Market(s)

Asia, Europe (main markets) New Zealand, Australia (Submarkets)

Coding

Coded - Design and coding required

Number of Pages Required

4 page

Requirements
Must have
• Home, Shop, About Us, Contact Us

Homepage to include:

Our Products
Company Video (video under construction)
What is MGO/KPS
Newsletter Opt-in

***(Not in Order)***

Please include 'Honey Product' mockups in website.
*Will add illustrator files in coming days
Nice to have
• FAQ & Partnership Inquiries (hyperlink in footer)

```html
<!DOCTYPE html>
<html lang="en">
<head>
<meta charset="utf-8">
<title>Rimu Vale Honey — Best Manuka Honey</title>
<link href="https://fonts.googleapis.com/css2?family=Jost:wght@400;500;600;700&family=Nunito+Sans:wght@400;600;700&display=swap" rel="stylesheet">
<style>
:root{
  --ink:#1f1f1f;
  --muted:#555;
  --gold-dark:#c4a25a;
  --gold-light:#f3e5a2;
  --gold-grad:linear-gradient(90deg,#c8a55e,#f2e4a0);
  --cream:#f7f0d2;
  --sky:#dbe9f1;
  --black:#000;
  --white:#fff;
}
*{box-sizing:border-box;margin:0;padding:0}
html,body{width:1200px;height:3838px;overflow:hidden}
body{position:relative;background:var(--white);font-family:"Nunito Sans",Arial,sans-serif;color:var(--ink)}
.abs{position:absolute}
h2.section-title{font-family:"Jost",Arial,sans-serif;font-weight:600;font-size:38px;letter-spacing:5px;text-transform:uppercase;color:#2a2a2a}
.gold-rule{height:4px;width:72px;background:var(--gold-grad);border-radius:2px}
.btn-gold{display:flex;align-items:center;justify-content:center;background:var(--gold-grad);border-radius:30px;font-family:"Jost",Arial,sans-serif;font-weight:600;font-size:13px;letter-spacing:2px;color:#4a3a18;text-transform:uppercase;box-shadow:0 0 0 3px #fff,0 0 0 5px #e6d49a}

/* header + hero */
.hero{left:0;top:0;width:1200px;height:740px;background:linear-gradient(180deg,#d3e4ee 0%,#e7f0f5 55%,#fff 100%)}
.hero-scene{left:0;top:180px;width:1200px;height:420px;background:radial-gradient(ellipse at 50% 20%,#c9d6df 0%,rgba(220,232,240,0) 60%)}
.brand{left:90px;top:26px;display:flex;align-items:center;gap:14px}
.brand-dot{width:40px;height:40px;border-radius:50%;background:#2d2d2d}
.brand-name{font-family:"Jost",Arial,sans-serif;font-weight:500;font-size:28px;letter-spacing:4px;color:#2d2d2d}
.main-nav{left:596px;top:38px;display:flex}
.main-nav a{font-family:"Jost",Arial,sans-serif;font-size:13px;font-weight:500;color:#222;text-decoration:none;letter-spacing:.5px}
.main-nav a.active{font-weight:700}
.hero-title{left:0;top:134px;width:1200px;text-align:center;font-family:"Jost",Arial,sans-serif;font-weight:600;font-size:56px;letter-spacing:6px;line-height:70px;color:#262626}
.hero-sub{left:0;top:206px;width:1200px;text-align:center;font-family:"Jost",Arial,sans-serif;font-weight:400;font-size:29px;letter-spacing:4px;color:#262626}
.hero-products{left:66px;top:300px;width:976px;height:420px;border-radius:40px;background:radial-gradient(ellipse at 50% 45%,#1a1412 0%,#3a2118 38%,rgba(150,60,40,.35) 60%,rgba(230,238,243,0) 75%)}
.arrow{top:326px}

/* MGO */
.mgo-blob{left:82px;top:760px;width:478px;height:478px}
.mgo-photo{left:124px;top:778px;width:420px;height:420px;border-radius:50%;background:radial-gradient(circle at 40% 40%,#e8a040 0%,#b98a4a 30%,#e9e6dc 60%,#9aa08a 100%)}
.mgo-jar{left:392px;top:996px;width:128px;height:232px;border-radius:20px;background:linear-gradient(180deg,#e6ef3a 0%,#1c1c1c 18%,#2a2a2a 70%,#e2a313 100%)}
.mgo-title{left:620px;top:822px}
.mgo-rule{left:622px;top:874px}
.mgo-copy{left:623px;top:900px;width:470px;font-size:13.5px;line-height:22px;color:var(--muted)}
.mgo-copy p+p{margin-top:21px}
.mgo-btn{left:623px;top:1110px;width:184px;height:50px}

/* products */
.products-bg{left:0;top:1218px;width:1200px;height:880px}
.products-title{left:0;top:1396px;width:1200px;text-align:center}
.products-rule{left:556px;top:1448px}
.product-card{top:1494px;width:307px;height:391px;background:var(--white);border-radius:60px;text-align:center;box-shadow:0 6px 20px rgba(160,130,60,.12)}
.product-shot{position:absolute;left:84px;top:48px;width:140px;height:166px;border-radius:18px;background:linear-gradient(180deg,#111 0 22%,#7a1020 22% 80%,#1a0a0a 80%)}
.product-name{position:absolute;left:0;width:100%;font-family:"Jost",Arial,sans-serif;font-weight:500;font-size:20px;color:#222}
.product-text{position:absolute;left:40px;width:227px;font-size:11.5px;line-height:19px;color:var(--muted)}
.product-card .btn-gold{position:absolute;left:79px;top:320px;width:152px;height:44px;font-size:11px}
.dots{left:568px;top:1941px;display:flex;gap:10px}
.dots span{width:12px;height:12px;border-radius:50%;background:#fff}
.dots span.on{background:#111}

/* video */
.video-title{left:0;top:2084px;width:1200px;text-align:center}
.video-rule{left:564px;top:2134px}
.video-intro{left:280px;top:2160px;width:640px;text-align:center;font-size:16.5px;line-height:22px;color:#555}
.video-frame{left:291px;top:2257px;width:609px;height:349px;background:radial-gradient(circle at 44% 22%,#a06212 0%,#6e5a46 20%,#7c7c7c 45%,#6a6a6a 100%);box-shadow:0 8px 24px rgba(0,0,0,.12)}
.video-label{left:291px;top:2418px;width:609px;text-align:center;font-family:"Jost",Arial,sans-serif;font-weight:600;font-size:20px;letter-spacing:3px;color:#fff}
.play{left:291px;top:2548px;width:79px;height:58px;background:var(--gold-grad);display:flex;align-items:center;justify-content:center}

/* faq */
.faq-bg{left:0;top:2660px;width:1200px;height:800px}
.faq-title{left:112px;top:2816px;font-family:"Jost",Arial,sans-serif;font-weight:700;font-size:38px;letter-spacing:3px;color:#fff}
.faq-rule{left:112px;top:2864px;width:76px;height:4px;background:#fff}
.faq-item{left:109px;width:490px;border:1.5px solid #6e5a2e;padding:0 26px;font-size:12.5px;font-weight:700;color:#2a2418;display:flex;align-items:center}
.faq-item.open{display:block;padding-top:20px}
.faq-item.open p{font-weight:400;font-size:11.5px;line-height:18px;margin-top:14px;color:#3a3324}
.faq-ring{left:662px;top:2820px;width:462px;height:462px;border-radius:50%;background:rgba(255,250,228,.55)}
.faq-photo{left:690px;top:2838px;width:430px;height:430px;border-radius:50%;background:radial-gradient(circle at 45% 60%,#f0a41c 0%,#d8b35a 30%,#e8dcc4 55%,#c99a48 100%)}

/* footer */
.footer{left:0;top:3441px;width:1200px;height:397px;background:var(--black)}
.footer-mark{left:582px;top:3408px;width:36px;height:36px;border-radius:50%;background:var(--gold-grad)}
.footer-col{top:3502px;color:var(--white)}
.footer-col h3{font-family:"Jost",Arial,sans-serif;font-weight:600;font-size:16px;letter-spacing:2.5px;text-transform:uppercase;margin-bottom:22px;color:var(--white)}
.footer-col ul{list-style:none}
.footer-col li{font-size:13px;height:30px;line-height:18px;padding-left:2px;color:var(--white)}
.footer-col li a{color:var(--white);text-decoration:none}
.social li{display:flex;align-items:center;gap:14px;height:34px}
.social i{width:11px;height:11px;border:1.5px solid #fff;border-radius:50%;display:inline-block}
.news-note{font-size:13px;margin-bottom:14px;padding-left:2px;color:var(--white)}
.news-input{width:232px;height:34px;background:#fff;color:#555;font-size:10px;letter-spacing:.5px;padding-left:18px;display:flex;align-items:center}
.news-btn{margin-top:12px;width:232px;height:36px;background:var(--gold-grad);color:#2c2310;font-family:"Jost",Arial,sans-serif;font-weight:600;font-size:13px;letter-spacing:1px;display:flex;align-items:center;justify-content:center}
.footer-line{left:0;top:3777px;width:1200px;height:1px;background:#2a2a2a}
.copyright{left:0;top:3797px;width:1200px;text-align:center;font-size:12px;color:#ddd}
</style>
</head>
<body>

<section class="abs hero" aria-label="Hero">
  <div class="abs hero-scene" role="img" aria-label="Misty snow-capped mountain landscape behind the products"></div>
</section>
<header>
  <div class="abs brand"><span class="brand-dot"></span><span class="brand-name">RIMU VALE HONEY</span></div>
  <nav class="abs main-nav">
    <a class="active" href="#" style="margin-right:68px">HOME</a>
    <a href="#" style="margin-right:77px">SHOP</a>
    <a href="#" style="margin-right:78px">ABOUT US</a>
    <a href="#">CONTACT US</a>
  </nav>
</header>
<h1 class="abs hero-title">BEST MANUKA HONEY</h1>
<p class="abs hero-sub">HONEY YOUR WILL NEVER TASTE!</p>
<div class="abs hero-products" role="img" aria-label="Three premium manuka honey jars in orange, black and crimson labels with manuka blossoms"></div>
<svg class="abs arrow" style="left:72px" width="30" height="50" viewBox="0 0 30 50"><path d="M26 4 6 25l20 21" fill="none" stroke="#8a9298" stroke-width="3"/></svg>
<svg class="abs arrow" style="left:1098px" width="30" height="50" viewBox="0 0 30 50"><path d="M4 4l20 21L4 46" fill="none" stroke="#8a9298" stroke-width="3"/></svg>

<svg class="abs mgo-blob" viewBox="0 0 478 478" aria-hidden="true">
  <defs><linearGradient id="blobGold" x1="0" y1="1" x2="1" y2="0"><stop offset="0" stop-color="#e9d698"/><stop offset="1" stop-color="#f6eecb"/></linearGradient></defs>
  <path d="M250 4C370 0 470 110 476 240c4 120-90 236-230 236C110 476 0 380 2 250 4 120 110 8 250 4z" fill="url(#blobGold)"/>
</svg>
<div class="abs mgo-photo" role="img" aria-label="Close-up of a honey bee on a white manuka flower"></div>
<div class="abs mgo-jar" role="img" aria-label="Rimu Vale Honey glass jar with yellow lid"></div>
<h2 class="abs section-title mgo-title">WHAT IS MGO</h2>
<div class="abs gold-rule mgo-rule"></div>
<div class="abs mgo-copy">
  <p>Lorem Ipsum is simply dummy text of the printing and typesetting industry. Lorem Ipsum has been the industry's standard dummy text ever since the 1500s, when an unknown printer took a galley of type and scrambled it to make a type specimen book. It has survived not only five centuries</p>
  <p>was popularised in the 1960s with the release of Lettersheet sheets containing Lorem Ipsum passages, and more recently with desktop publishing software like Folio Layout Studio including versions of Lorem Ipsum</p>
</div>
<a class="abs btn-gold mgo-btn">LEARN MORE</a>

<svg class="abs products-bg" viewBox="0 0 1200 880" preserveAspectRatio="none" role="img" aria-label="Soft-focus manuka blossoms in cream and pale gold">
  <defs><radialGradient id="bloom" cx="50%" cy="50%" r="70%"><stop offset="0" stop-color="#f8f1d6"/><stop offset=".6" stop-color="#efe2b4"/><stop offset="1" stop-color="#e7d7a6"/></radialGradient></defs>
  <path d="M0 0Q600 210 1200 0V880Q600 720 0 880Z" fill="url(#bloom)"/>
</svg>
<h2 class="abs section-title products-title">OUR PRODUCTS</h2>
<div class="abs gold-rule products-rule"></div>

<article class="abs product-card" style="left:106px">
  <div class="product-shot" role="img" aria-label="Manuka honey jar with red label"></div>
  <h3 class="product-name" style="top:236px">Mounka Honey</h3>
  <p class="product-text" style="top:264px">Lorem Ipsum is simply dummy text of the printing ly dummy text</p>
  <a class="btn-gold">LEARN MORE</a>
</article>
<article class="abs product-card" style="left:435px">
  <div class="product-shot" style="background:linear-gradient(180deg,#111 0 22%,#4b2a7a 22% 82%,#1a0a1a 82%)" role="img" aria-label="Manuka honey jar with purple label"></div>
  <h3 class="product-name" style="top:228px">Mounka Honey</h3>
  <p class="product-text" style="top:256px">Lorem Ipsum is simply dummy text of the printing ly dummy text</p>
  <a class="btn-gold">LEARN MORE</a>
</article>
<article class="abs product-card" style="left:773px">
  <div class="product-shot" style="background:linear-gradient(180deg,#1a1a1a 0%,#222 100%)" role="img" aria-label="Manuka honey jar with black label"></div>
  <h3 class="product-name" style="top:232px">Mounka Honey</h3>
  <p class="product-text" style="top:260px">Lorem Ipsum is simply dummy text of the printing ly dummy text</p>
  <a class="btn-gold">LEARN MORE</a>
</article>
<div class="abs dots"><span class="on"></span><span></span><span></span></div>

<h2 class="abs section-title video-title">OUR COMPANY VIDEO</h2>
<div class="abs gold-rule video-rule"></div>
<p class="abs video-intro">Lorem Ipsum is simply dummy text of the printing and typesetting industry. Lorem Ipsum has been the industry's standard dummy.</p>
<div class="abs video-frame" role="img" aria-label="Bowl of honey with wooden dipper beside manuka sprigs"></div>
<div class="abs video-label">PLAY VIDEO</div>
<div class="abs play"><svg width="20" height="24" viewBox="0 0 20 24"><path d="M0 0l20 12L0 24z" fill="#000"/></svg></div>

<svg class="abs faq-bg" viewBox="0 0 1200 800" preserveAspectRatio="none" aria-hidden="true">
  <defs><linearGradient id="faqGold" x1="0" y1="0" x2="1" y2="0"><stop offset="0" stop-color="#efe1a6"/><stop offset=".5" stop-color="#e9d594"/><stop offset="1" stop-color="#d6b56a"/></linearGradient></defs>
  <path d="M0 0Q600 220 1200 0V781Q600 600 0 781Z" fill="url(#faqGold)"/>
  <path d="M0 781Q600 600 1200 781V800H0Z" fill="#000"/>
</svg>
<h2 class="abs faq-title">FAQ</h2>
<div class="abs faq-rule"></div>
<div class="abs faq-item" style="top:2920px;height:48px">Lorem ipsum dolor sit amet, consectetur adipiscing elit</div>
<div class="abs faq-item" style="top:2975px;height:48px">Sed do eiusmod tempor incididunt ut labore</div>
<div class="abs faq-item" style="top:3032px;height:48px">Et dolore magna aliqua. Ut enim ad minim</div>
<div class="abs faq-item open" style="top:3089px;height:126px">Veniam quis nostrud exercitation ullamco laboris nisi
  <p>Lorem Ipsum is simply dummy text of the printing and typesetting industry.<br>Lorem Ipsum has been the industry's standard dummy.</p>
</div>
<div class="abs faq-ring"></div>
<div class="abs faq-photo" role="img" aria-label="Spoon of golden honey with white flowers and honeycomb on bamboo mat"></div>

<footer class="abs footer"></footer>
<div class="abs footer-mark"></div>
<div class="abs footer-col" style="left:133px">
  <h3>Navigation</h3>
  <ul><li><a href="#">Home</a></li><li><a href="#">About Us</a></li><li><a href="#">Products</a></li><li><a href="#">Videos</a></li><li><a href="#">Cotnact Us</a></li></ul>
</div>
<div class="abs footer-col" style="left:350px">
  <h3>Useful Links</h3>
  <ul><li><a href="#">FAQ</a></li><li><a href="#">Partnership Inquiries</a></li><li><a href="#">Terms</a></li><li><a href="#">Shipping &amp; Return</a></li><li><a href="#">Cart</a></li></ul>
</div>
<div class="abs footer-col" style="left:604px">
  <h3>Newsletter Sign Up</h3>
  <p class="news-note">Sign up here to stay up to date</p>
  <div class="news-input">EMAIL ADDRESS</div>
  <div class="news-btn">SUBSCRIBE</div>
</div>
<div class="abs footer-col social" style="left:932px">
  <h3>Get In Touch</h3>
  <ul><li><i></i>Feedline</li><li><i></i>Chirper</li><li><i></i>Snapgram</li><li><i></i>WorkNet</li></ul>
</div>
<div class="abs footer-line"></div>
<p class="abs copyright">Copyright © 2021 Rimu Vale Honey</p>

</body>
</html>
```